KLV Plant Services

We are a heavy diesel mechanical business with additional air con certificates, remapping engine rebuilt

Contact Information for Business Card

Company Name, Director Name, Managing Director, Contact details, email and website

Font styles to use
Serif
Script

```html
<!DOCTYPE html>
<html lang="en">
<head>
<meta charset="utf-8">
<title>KLV Plant Services – Business Card</title>
<link href="https://fonts.googleapis.com/css2?family=Montserrat:wght@400;500;700&display=swap" rel="stylesheet">
<style>
  :root {
    --backdrop: #d3d3d3;
    --card: #ffffff;
    --navy: #15146e;
    --ink: #1b1b1b;
    --rule: #2a2a2a;
  }
  html, body {
    margin: 0;
    padding: 0;
    width: 1146px;
    height: 1200px;
    overflow: hidden;
    background: var(--backdrop);
    font-family: "Montserrat", sans-serif;
  }
  .canvas {
    position: relative;
    width: 1146px;
    height: 1200px;
  }
  .card {
    position: absolute;
    left: 235px;
    width: 686px;
    height: 393px;
    background: var(--card);
  }
  .card--front { top: 145px; }
  .card--back  { top: 621px; }

  .company-name {
    position: absolute;
    margin: 0;
    color: var(--ink);
    font-weight: 500;
    line-height: 1;
    white-space: nowrap;
  }
  .card--front .company-name {
    left: 38px;
    top: 106px;
    font-size: 24px;
  }
  .card--back .company-name {
    left: 0;
    right: 0;
    top: 170px;
    text-align: center;
    font-size: 34px;
  }

  .person {
    position: absolute;
    right: 37px;
    top: 212px;
    text-align: right;
  }
  .person__name {
    margin: 0;
    color: var(--navy);
    font-size: 33px;
    font-weight: 700;
    letter-spacing: 0.5px;
    line-height: 1;
  }
  .person__role {
    margin: 9px 0 0;
    color: var(--ink);
    font-size: 17px;
    font-weight: 500;
    line-height: 1;
  }
  .accent-bar {
    position: absolute;
    right: 0;
    top: 215px;
    width: 13px;
    height: 49px;
    background: var(--navy);
  }
  .divider {
    position: absolute;
    left: 36px;
    width: 629px;
    top: 281px;
    height: 1.5px;
    background: var(--rule);
  }
  .contact-list {
    position: absolute;
    left: 37px;
    top: 292px;
    margin: 0;
    padding: 0;
    list-style: none;
  }
  .contact-list li {
    display: flex;
    align-items: center;
    height: 27px;
    font-size: 18.5px;
    color: var(--ink);
  }
  .contact-list svg {
    width: 18px;
    height: 18px;
    margin-right: 9px;
    fill: var(--navy);
    flex: none;
  }
  .address {
    position: absolute;
    right: 37px;
    top: 312px;
    margin: 0;
    text-align: right;
    font-style: normal;
    font-size: 18.5px;
    line-height: 27px;
    color: var(--ink);
  }
</style>
</head>
<body>
<main class="canvas">

  <section class="card card--front" aria-label="Business card front">
    <p class="company-name">KLV Plant Services</p>

    <div class="person">
      <h1 class="person__name">DANIEL CARTER</h1>
      <p class="person__role">MANAGING DIRECTOR</p>
    </div>
    <div class="accent-bar"></div>

    <div class="divider"></div>

    <ul class="contact-list">
      <li>
        <svg viewBox="0 0 24 24" aria-hidden="true"><path d="M6.6 10.8a15.1 15.1 0 0 0 6.6 6.6l2.2-2.2a1 1 0 0 1 1-.25 11.4 11.4 0 0 0 3.6.57 1 1 0 0 1 1 1V20a1 1 0 0 1-1 1A17 17 0 0 1 3 4a1 1 0 0 1 1-1h3.5a1 1 0 0 1 1 1c0 1.25.2 2.45.57 3.6a1 1 0 0 1-.25 1z"/></svg>
        044-123 456 789
      </li>
      <li>
        <svg viewBox="0 0 24 24" aria-hidden="true"><path d="M2 5h20v14H2z M3.5 6.5 12 13l8.5-6.5v1.8L12 15 3.5 8.3z" fill-rule="evenodd"/></svg>
        info@webname.com
      </li>
      <li>
        <svg viewBox="0 0 24 24" aria-hidden="true"><path d="M12 2a10 10 0 1 0 0 20 10 10 0 0 0 0-20zm6.9 6h-2.9a15.6 15.6 0 0 0-1.4-3.6A8 8 0 0 1 18.9 8zM12 4c.8 1.2 1.5 2.5 1.9 4h-3.8c.4-1.5 1.1-2.8 1.9-4zM4.3 14a8.2 8.2 0 0 1 0-4h3.4a16.5 16.5 0 0 0 0 4zm.8 2h2.9c.3 1.3.8 2.5 1.4 3.6A8 8 0 0 1 5.1 16zM8 8H5.1a8 8 0 0 1 4.3-3.6C8.8 5.5 8.3 6.7 8 8zm4 12c-.8-1.2-1.5-2.5-1.9-4h3.8c-.4 1.5-1.1 2.8-1.9 4zm2.3-6H9.7a14.7 14.7 0 0 1 0-4h4.6a14.7 14.7 0 0 1 0 4zm.3 5.6c.6-1.1 1.1-2.3 1.4-3.6h2.9a8 8 0 0 1-4.3 3.6zm1.7-5.6a16.5 16.5 0 0 0 0-4h3.4a8.2 8.2 0 0 1 0 4z"/></svg>
        www.websitename.com
      </li>
    </ul>

    <address class="address">
      421, Address line goes here<br>
      45452, Country name
    </address>
  </section>

  <section class="card card--back" aria-label="Business card back">
    <p class="company-name">KLV Plant Services</p>
  </section>

</main>
</body>
</html>
```